Quill Physical Therapy Website

I would need a clean modern website built to showcase my Physical therapy brand and services. I would need a simple but descriptive website that can ultimately connect my patients to my electronic medical portal so they may book an appointment..

```html
<!DOCTYPE html>
<html lang="en">
<head>
<meta charset="utf-8">
<title>Quill Physical Therapy &amp; Wellness</title>
<link href="https://fonts.googleapis.com/css2?family=Montserrat:wght@400;500;600;700;800&display=swap" rel="stylesheet">
<style>
:root{
  --teal:#13908a;
  --teal-dark:#0c7a76;
  --green:#7cc242;
  --green-soft:#8fcb55;
  --ink:#1d2a38;
  --text:#555f69;
  --white:#ffffff;
  --line:#d9e2e2;
  --grey:#e9eaea;
}
*{box-sizing:border-box;margin:0;padding:0}
html,body{width:1200px;height:4135px;overflow:hidden;background:var(--white)}
body{font-family:"Montserrat",sans-serif;color:var(--ink)}
.page{position:relative;width:1200px;height:4135px;overflow:hidden}
.abs{position:absolute}

/* header */
.site-header{position:absolute;left:0;top:0;width:1200px;height:108px;background:var(--white);z-index:5}
.brand{position:absolute;left:104px;top:22px;display:flex;align-items:center;gap:12px}
.brand-dot{width:52px;height:52px;border-radius:50%;background:var(--teal)}
.brand-name{font-weight:800;font-size:40px;color:var(--teal);letter-spacing:1px}
.call-btn{position:absolute;left:818px;top:0;width:266px;height:35px;background:var(--teal-dark);color:var(--white);border-radius:0 0 6px 6px;font-size:12.5px;font-weight:600;display:flex;align-items:center;justify-content:center;gap:8px;letter-spacing:.5px}
.main-nav a{position:absolute;top:66px;font-size:12.5px;font-weight:600;color:var(--ink);text-decoration:none;letter-spacing:.3px}
.main-nav a.active{color:var(--teal)}
.nav-underline{position:absolute;left:362px;top:104px;width:48px;height:4px;background:var(--green)}

/* hero */
.hero-photo{position:absolute;left:0;top:108px;width:1200px;height:690px;background:linear-gradient(100deg,#eef2f4 0%,#e5ebee 40%,#d9dfe3 70%,#c9d0d5 100%)}
.hero-ring{position:absolute;left:85px;top:168px;width:466px;height:466px;border-radius:50%;background:conic-gradient(from 200deg,var(--green) 0deg,var(--teal) 180deg,rgba(19,144,138,.15) 300deg,var(--green) 360deg);}
.hero-ring::after{content:"";position:absolute;inset:22px;border-radius:50%;background:radial-gradient(circle at 45% 45%,#ffffff 0%,#f3f7f7 60%,#e4eeee 100%)}
.hero-text{position:absolute;left:118px;top:312px;width:400px;text-align:center;z-index:2}
.hero-kicker{font-size:22px;font-weight:500;color:var(--teal);letter-spacing:2px}
.hero-title{font-size:41px;font-weight:700;color:var(--teal-dark);letter-spacing:1px;margin-top:6px;line-height:1}
.hero-sub{font-size:28px;font-weight:700;color:var(--green);letter-spacing:1px;margin-top:8px}
.btn-solid{position:absolute;left:210px;top:452px;width:213px;height:44px;border-radius:22px;background:var(--teal-dark);color:var(--white);font-size:12px;font-weight:700;letter-spacing:.8px;display:flex;align-items:center;justify-content:center;z-index:2}
.hero-arrow{position:absolute;top:385px;width:16px;height:30px}

/* section headings */
.kicker{font-size:15px;font-weight:700;letter-spacing:3px;color:var(--teal)}
.title{font-size:36px;font-weight:700;letter-spacing:1.5px;color:var(--ink);line-height:1.1;white-space:nowrap}
.title span{color:var(--teal)}
.body-copy{font-size:13.5px;line-height:29px;color:var(--text)}
.btn-outline{height:47px;border:2px solid var(--teal);border-radius:24px;color:var(--teal);font-size:12.5px;font-weight:700;letter-spacing:.8px;display:flex;align-items:center;justify-content:center}

/* about */
.about-figure{position:absolute;left:150px;top:785px;width:280px;height:530px;background:linear-gradient(180deg,rgba(240,244,246,0) 0%,#eef3f5 40%,#e2e9ec 100%);border-radius:140px 140px 60px 60px}
.about-photo{position:absolute;left:201px;top:786px;width:320px;height:320px;border-radius:50%;background:linear-gradient(135deg,#d6dee3,#8fc5d8 55%,#4d8fa8);border:6px solid var(--white);box-shadow:0 0 0 3px #c5ccd0}
.about-text{position:absolute;left:589px;top:868px;width:480px}

/* services */
.services-heading{position:absolute;left:0;width:1200px;text-align:center}
.service{position:absolute;border-radius:50%;display:flex;flex-direction:column;align-items:center;justify-content:flex-end;text-align:center;color:var(--white);overflow:hidden}
.service-name{font-size:17px;font-weight:600;letter-spacing:.5px}
.service-desc{font-size:12.5px;line-height:20px;margin-top:6px;width:230px;opacity:.95}
.service-icon{width:36px;height:36px;border:2px solid var(--white);border-radius:50%;margin-top:18px;display:flex;align-items:center;justify-content:center}

/* why */
.why-photo{position:absolute;left:545px;top:1985px;width:655px;height:620px;background:linear-gradient(120deg,#eef2f4 0%,#d8e2e7 45%,#b8c7cf 100%)}
.why-text{position:absolute;left:144px;top:2124px;width:395px}

/* blogs */
.blog-card{position:absolute;top:2687px;width:308px;height:353px;background:var(--white);border-radius:0 28px 0 28px;box-shadow:0 6px 24px rgba(0,0,0,.12);overflow:hidden}
.blog-img{width:308px;height:197px}
.blog-body{padding:24px 35px 0 35px}
.blog-date{font-size:11px;font-weight:600;color:var(--green)}
.blog-title{font-size:13px;font-weight:700;color:var(--teal-dark);margin-top:9px;letter-spacing:.5px}
.blog-text{font-size:10.5px;line-height:18px;color:var(--text);margin-top:8px}

/* booking */
.booking{position:absolute;left:0;top:3152px;width:1200px;height:585px;background:linear-gradient(180deg,#16a09a,#108781)}
.booking-head{position:absolute;left:128px;top:3233px}
.field{position:absolute;left:124px;width:381px;height:42px;border-radius:21px;background:var(--white);font-size:12px;font-weight:600;color:var(--ink);padding:13px 24px}
.field.message{height:98px;border-radius:14px}
.btn-submit{position:absolute;left:128px;top:3584px;width:154px;height:40px;border-radius:20px;background:var(--green);color:var(--white);font-size:11.5px;font-weight:700;letter-spacing:1px;display:flex;align-items:center;justify-content:center}

/* footer */
.footer-brand{position:absolute;left:140px;top:3795px;width:205px;text-align:center}
.footer-brand .brand-dot{width:90px;height:90px;margin:0 auto 28px}
.footer-brand .brand-name{font-size:48px}
.footer-col{position:absolute;top:3808px}
.footer-col h4{font-size:15px;font-weight:700;color:var(--teal);letter-spacing:.5px;margin-bottom:8px}
.footer-col li{list-style:none;font-size:12px;color:var(--ink);line-height:27.5px}
.contact-line{display:flex;align-items:flex-start;gap:10px;font-size:12px;line-height:23px;color:var(--ink)}
.contact-line svg{flex:none;margin-top:4px}
.socials{display:flex;gap:4px;margin-top:14px;margin-left:-12px}
.socials span{width:26px;height:26px;border:1.5px solid var(--teal);border-radius:50%}
.copyright{position:absolute;left:0;top:4063px;width:1200px;height:72px;background:var(--grey);font-size:11.5px;color:#9aa1a6;display:flex;align-items:center;justify-content:center}
</style>
</head>
<body>
<div class="page">

  <!-- header -->
  <header class="site-header">
    <div class="brand"><span class="brand-dot"></span><span class="brand-name">QUILL</span></div>
    <div class="call-btn">
      <svg width="13" height="13" viewBox="0 0 24 24" fill="#fff"><path d="M6.6 10.8c1.4 2.8 3.8 5.1 6.6 6.6l2.2-2.2c.3-.3.7-.4 1-.2 1.1.4 2.3.6 3.6.6.6 0 1 .4 1 1V20c0 .6-.4 1-1 1C10.6 21 3 13.4 3 4c0-.6.4-1 1-1h3.5c.6 0 1 .4 1 1 0 1.3.2 2.5.6 3.6.1.3 0 .7-.2 1L6.6 10.8z"/></svg>
      CALL US NOW +100 555 0182
    </div>
    <nav class="main-nav">
      <a class="active" style="left:364px">HOME</a>
      <a style="left:454px">ABOUT US</a>
      <a style="left:565px">OUR SERVICES</a>
      <a style="left:706px">WHY CHOOSE US</a>
      <a style="left:861px">TESTIMONIALS</a>
      <a style="left:1001px">CONTACT US</a>
    </nav>
    <span class="nav-underline"></span>
  </header>

  <!-- hero -->
  <section class="hero">
    <div class="hero-photo" role="img" aria-label="Smiling therapist stretching a patient's shoulder on a treatment table"></div>
    <div class="hero-ring"></div>
    <div class="hero-text">
      <div class="hero-kicker">WELCOME TO</div>
      <div class="hero-title">QUILL PHYSICAL</div>
      <div class="hero-sub">THERAPY &amp; WELLNESS</div>
    </div>
    <div class="btn-solid">BOOK APPOINTMENT</div>
    <svg class="hero-arrow" style="left:28px" viewBox="0 0 16 30"><path d="M14 2 2 15l12 13" fill="none" stroke="#fff" stroke-width="3"/></svg>
    <svg class="hero-arrow" style="left:1160px" viewBox="0 0 16 30"><path d="M2 2l12 13L2 28" fill="none" stroke="#fff" stroke-width="3"/></svg>
    <svg class="abs" style="left:0;top:690px" width="1200" height="110" viewBox="0 0 1200 110">
      <path d="M0 110 L0 100 C250 10 520 40 760 80 C950 110 1100 70 1200 20 L1200 110 Z" fill="#fff"/>
      <path d="M0 100 C250 10 520 40 760 80 C950 110 1100 70 1200 20" fill="none" stroke="#13908a" stroke-width="7"/>
      <path d="M520 45 C650 60 760 85 860 88 C980 90 1090 60 1200 10" fill="none" stroke="#7cc242" stroke-width="3"/>
    </svg>
  </section>

  <!-- about -->
  <section class="about">
    <div class="about-figure" role="img" aria-label="Line illustration of a head and neck silhouette"></div>
    <div class="about-photo" role="img" aria-label="Therapist treating a patient's arm"></div>
    <div class="about-text">
      <div class="kicker">WHO WE ARE</div>
      <h2 class="title" style="margin-top:6px">ABOUT <span>QUILL</span></h2>
      <p class="body-copy" style="margin-top:30px">Lorem Ipsum is simply dummy text of the printing and typesetting industry. Lorem Ipsum has been the industry's standard dummy text ever since the 1500s, when an unknown printer took a galley of type and scrambled it to make a type specimen book. It has survived not only five centuries, but also the leap into electronic typesetting, remaining essentially unchanged. Lorem Ipsum is simply dummy.</p>
      <div class="btn-outline" style="width:169px;margin-top:32px;margin-left:-4px">LEARN MORE</div>
    </div>
  </section>

  <!-- services -->
  <section class="services">
    <svg class="abs" style="left:0;top:1300px" width="1200" height="740" viewBox="0 0 1200 740">
      <path d="M0 105 C300 20 700 50 900 70 C1050 80 1140 40 1200 0 L1200 630 C1080 650 900 645 700 640 C450 635 200 650 0 730 Z" fill="#13908a"/>
      <path d="M0 105 C300 20 700 50 900 70 C1050 80 1140 40 1200 0" fill="none" stroke="#7cc242" stroke-width="7"/>
      <path d="M0 740 L0 730 C200 650 450 635 700 640 C900 645 1080 650 1200 630 L1200 740 Z" fill="#fff"/>
      <path d="M0 730 C200 650 450 635 700 640 C900 645 1080 650 1200 630" fill="none" stroke="#7cc242" stroke-width="7"/>
    </svg>
    <div class="services-heading" style="top:1418px">
      <div class="kicker" style="color:#fff">WHAT WE DO</div>
      <h2 class="title" style="color:#fff;font-size:32px;margin-top:6px">SERVICES PROVIDE</h2>
    </div>
    <span class="abs" style="left:549px;top:1482px;width:89px;height:4px;background:var(--green)"></span>

    <div class="service" style="left:103px;top:1530px;width:346px;height:346px;background:linear-gradient(180deg,#c8d1d6 0%,#7f9099 50%,#2b3a44 100%);padding-bottom:42px" role="img" aria-label="Therapist stretching a patient's leg">
      <div class="service-name">PHYSICAL THERAPY</div>
      <div class="service-desc">Lorem ipsum dolor sit amet, consectetur adipiscing elit sed.</div>
    </div>
    <div class="service" style="left:744px;top:1530px;width:346px;height:346px;background:linear-gradient(180deg,#d9b89a 0%,#8c7565 50%,#2f3438 100%);padding-bottom:46px" role="img" aria-label="Woman receiving a relaxing head massage">
      <div class="service-name">WELLNESS THERAPY</div>
      <div class="service-desc">Lorem ipsum dolor sit amet, consectetur adipiscing elit sed do.</div>
    </div>
    <div class="service" style="left:410px;top:1516px;width:374px;height:374px;background:radial-gradient(circle at 50% 40%,#8fcb55,#67ad33);border:8px solid #fff;justify-content:center;padding-top:60px" role="img" aria-label="Injury pain treatment scene in green tint">
      <div class="service-name">INJURY PAIN</div>
      <div class="service-desc">Lorem ipsum dolor sit amet, consectetur adipiscing elit sed.or sit amet-consectetur adipiscing.</div>
      <div class="service-icon"><svg width="14" height="10" viewBox="0 0 14 10"><path d="M2 2l5 5 5-5" fill="none" stroke="#fff" stroke-width="2"/></svg></div>
    </div>
  </section>

  <!-- why choose -->
  <section class="why">
    <div class="why-photo" role="img" aria-label="Therapist assessing a woman's shoulder mobility in a clinic"></div>
    <svg class="abs" style="left:0;top:2500px" width="1200" height="120" viewBox="0 0 1200 120">
      <path d="M0 120 L0 100 C200 80 400 60 560 80 C800 110 1000 120 1200 100 L1200 120 Z" fill="#fff"/>
    </svg>
    <div class="why-text">
      <div class="kicker">WHY WE ARE</div>
      <h2 class="title" style="margin-top:6px;font-size:32px">WHY CHOOSE <span>QUILL</span></h2>
      <p class="body-copy" style="margin-top:24px">Lorem Ipsum is simply dummy text of the printing and typesetting industry. Lorem Ipsum has been the industry's standard dummy text ever since the 1500s, when an unknown printer took a galley of type and scrambled it to make a type specimen book. It has survived</p>
      <div class="btn-outline" style="width:161px;margin-top:20px;margin-left:-3px">LEARN MORE</div>
    </div>
  </section>

  <!-- blogs -->
  <section class="blogs">
    <h2 class="title abs" style="left:0;top:2600px;width:1200px;text-align:center;font-size:32px">LATEST <span>BLOGS</span></h2>
    <span class="abs" style="left:551px;top:2642px;width:98px;height:4px;background:var(--green)"></span>

    <article class="blog-card" style="left:117px">
      <div class="blog-img" role="img" aria-label="Patient exercising leg with a resistance band" style="background:linear-gradient(135deg,#e9e6e1,#bfb8ad)"></div>
      <div class="blog-body">
        <div class="blog-date">25 SEP 2021</div>
        <div class="blog-title">LOREM IPSUM DOLOR SIT</div>
        <div class="blog-text">Lorem ipsum dolor sit amet, consectetur adipiscing elit, sed do eiusmod tempor incididunt ut labore et dolore magna aliqua.</div>
      </div>
    </article>
    <article class="blog-card" style="left:449px">
      <div class="blog-img" role="img" aria-label="Back massage with candles" style="background:linear-gradient(135deg,#c9a587,#7a5c47)"></div>
      <div class="blog-body">
        <div class="blog-date">25 SEP 2021</div>
        <div class="blog-title">LOREM IPSUM DOLOR SIT</div>
        <div class="blog-text">Lorem ipsum dolor sit amet, consectetur adipiscing elit, sed do eiusmod tempor incididunt ut labore et dolore magna aliqua.</div>
      </div>
    </article>
    <article class="blog-card" style="left:780px">
      <div class="blog-img" role="img" aria-label="Facial skin treatment" style="background:linear-gradient(135deg,#d8c5c0,#a88a86)"></div>
      <div class="blog-body">
        <div class="blog-date">25 SEP 2021</div>
        <div class="blog-title">LOREM IPSUM DOLOR SIT</div>
        <div class="blog-text">Lorem ipsum dolor sit amet, consectetur adipiscing elit, sed do eiusmod tempor incididunt ut labore et dolore magna aliqua.</div>
      </div>
    </article>
  </section>

  <!-- booking -->
  <section>
    <div class="booking"></div>
    <svg class="abs" style="left:0;top:3152px" width="1200" height="585" viewBox="0 0 1200 585">
      <path d="M1200 14 C900 20 650 90 600 250 C560 380 520 500 455 585 L1200 585 Z" fill="#7cc242"/>
      <path d="M1200 28 C910 34 670 104 618 256 C580 385 545 500 485 585 L1200 585 Z" fill="#d9a08a" role="img" aria-label="Hands pressing a patient's back with the spine highlighted"/>
    </svg>
    <div class="booking-head">
      <div class="kicker" style="color:#fff">GET IN TOUCH</div>
      <h2 class="title" style="color:#fff;font-size:32px;margin-top:4px">BOOK APPOINTMENT</h2>
    </div>
    <span class="abs" style="left:128px;top:3291px;width:93px;height:4px;background:var(--green)"></span>
    <div class="field" style="top:3319px">Name*</div>
    <div class="field" style="top:3370px">Email address*</div>
    <div class="field" style="top:3421px">Phone*</div>
    <div class="field message" style="top:3476px;left:128px;width:377px">Message</div>
    <div class="btn-submit">SUBMIT NOW</div>
  </section>

  <!-- footer -->
  <footer>
    <div class="footer-brand">
      <div class="brand-dot"></div>
      <div class="brand-name">QUILL</div>
    </div>
    <div class="footer-col" style="left:441px">
      <h4>NAVIGATE</h4>
      <ul><li>Home</li><li>About Us</li><li>Our Services</li><li>New Products</li><li>Contact Us</li></ul>
    </div>
    <div class="footer-col" style="left:638px">
      <h4>RESOURCES</h4>
      <ul><li>News</li><li>Testimonials</li><li>Privacy Policy</li><li>Terms &amp; Condition</li></ul>
    </div>
    <div class="footer-col" style="left:855px">
      <h4>CONTACT US</h4>
      <div class="contact-line"><svg width="13" height="15" viewBox="0 0 12 16"><path d="M6 0C2.7 0 0 2.6 0 5.9 0 10.3 6 16 6 16s6-5.7 6-10.1C12 2.6 9.3 0 6 0zm0 8.2a2.3 2.3 0 1 1 0-4.6 2.3 2.3 0 0 1 0 4.6z" fill="#13908a"/></svg><div>Office Lindenfeld | Birchway 14<br>Office Marrow Vale | Eastgate 9</div></div>
      <div class="contact-line"><svg width="13" height="13" viewBox="0 0 24 24"><path d="M6.6 10.8c1.4 2.8 3.8 5.1 6.6 6.6l2.2-2.2c.3-.3.7-.4 1-.2 1.1.4 2.3.6 3.6.6.6 0 1 .4 1 1V20c0 .6-.4 1-1 1C10.6 21 3 13.4 3 4c0-.6.4-1 1-1h3.5c.6 0 1 .4 1 1 0 1.3.2 2.5.6 3.6.1.3 0 .7-.2 1L6.6 10.8z" fill="#13908a"/></svg><div>Tel: (1300) 555 0147</div></div>
      <div class="contact-line"><svg width="13" height="11" viewBox="0 0 14 11"><path d="M0 0h14v11H0z" fill="#13908a"/><path d="M0 0l7 6 7-6" fill="none" stroke="#fff" stroke-width="1.3"/></svg><div>Email: hello@quillphysio.example</div></div>
      <div class="socials"><span></span><span></span><span></span></div>
    </div>
    <div class="copyright">© 2021 Quill Studio | All Rights Reserved &nbsp;|&nbsp; Terms &amp; Condition</div>
  </footer>

</div>
</body>
</html>
```